Business Card Design Project for an English Teacher

I need a business card design for my new job.
I'd like to start teaching English as a freelance.
My students will be children, teenager, and adults, who don't like or hesitate to study English and I would like to open a door to the new world for them.

I'd like to put the information below;
[right side]
1. name
2. mail address
3. mobile number
4. website or facebook page

[back]
1.my message: Feel free at asking me anything about my classes

2.lesson list such as:
price: 3150 yen ~

calsses:
kids class( mum& dad can join) ... 30 minutes / 45 minutes
students (over age 13).... 60minutes / 90 minutes
Adult (over age 19) .... 60 minutes / 90 minutes

3. I'll have both Web Lesson and Face to Face Lesson

4. Free trial lesson

Target Market(s)

My students will be children, teenager, and adults, who don't like or hesitate to study English

Industry/Entity Type

Business

Requirements
Must have
• designed both side

```html
<!DOCTYPE html>
<html lang="en">
<head>
<meta charset="utf-8">
<title>Haruna Aoki – English Instructor Business Card</title>
<link rel="stylesheet" href="https://fonts.googleapis.com/css2?family=Arimo:wght@400;700&family=Questrial&display=swap">
<style>
  :root {
    --page-bg: #d9d9d9;
    --card-white: #ffffff;
    --teal: #0e7a9a;
    --ink: #1b1b1b;
    --ink-soft: #333333;
    --on-teal: #ffffff;
    --rule-on-teal: rgba(255,255,255,0.85);
  }
  * { box-sizing: border-box; margin: 0; padding: 0; }
  html, body { width: 1200px; height: 900px; overflow: hidden; }
  body {
    background: var(--page-bg);
    position: relative;
    font-family: "Questrial", "Century Gothic", sans-serif;
  }
  .card {
    position: absolute;
    width: 597px;
    height: 331px;
    box-shadow: 0 3px 8px rgba(0,0,0,0.35);
    overflow: hidden;
  }

  /* Front */
  .card-front { left: 126px; top: 92px; background: var(--card-white); }
  .front-band {
    position: absolute; left: 0; bottom: 0; width: 100%; height: 11px;
    background: var(--teal);
  }
  .brand {
    position: absolute; right: 36px; top: 44px;
    display: flex; align-items: center; gap: 10px;
    font-family: "Questrial", sans-serif;
    font-size: 31px; color: var(--teal); letter-spacing: 1px;
  }
  .brand-dot { width: 16px; height: 16px; border-radius: 50%; background: var(--teal); }
  .stairs { position: absolute; left: 0; top: 0; }
  .person-name {
    position: absolute; left: 38px; top: 164px;
    font-family: "Arimo", Arial, sans-serif; font-weight: 700;
    font-size: 41px; color: var(--ink); letter-spacing: -0.3px;
  }
  .person-role {
    position: absolute; left: 39px; top: 207px;
    font-family: "Arimo", Arial, sans-serif; font-size: 14.5px; color: var(--ink-soft);
  }
  .contact-list {
    position: absolute; list-style: none;
    font-family: "Questrial", sans-serif; color: var(--ink-soft);
  }
  .contact-list li { display: flex; align-items: center; gap: 9px; height: 18.5px; white-space: nowrap; }
  .contact-primary { left: 37px; top: 246px; font-size: 12px; }
  .contact-primary li:first-child { font-size: 14px; }
  .contact-social { left: 233px; top: 235px; font-size: 11.5px; }
  .contact-icon {
    width: 13px; height: 13px; border-radius: 50%; background: var(--teal);
    flex: none; display: block;
  }

  /* Back */
  .card-back { left: 469px; top: 470px; background: var(--card-white); }
  .back-panel {
    position: absolute; left: 0; top: 0; width: 100%; height: 320px;
    background: var(--teal);
    color: var(--on-teal);
  }
  .quote {
    position: absolute; left: 112px; top: 61px;
    font-size: 27.5px; line-height: 33px; letter-spacing: 0.1px;
  }
  .quote-mark {
    position: absolute; font-family: Georgia, "Times New Roman", serif;
    font-size: 80px; line-height: 1; font-weight: 700;
  }
  .quote-open { left: 56px; top: 48px; }
  .quote-close { left: 354px; top: 92px; }
  .divider {
    position: absolute; left: 59px; top: 156px; width: 481px; height: 1px;
    background: var(--rule-on-teal);
  }
  .classes-title { position: absolute; left: 65px; top: 176px; font-size: 22px; font-weight: 400; }
  .class-list { position: absolute; left: 91px; top: 207px; list-style: none; font-size: 14.5px; }
  .class-list li { display: flex; height: 21.3px; align-items: center; white-space: nowrap; }
  .class-name::before { content: "\2605"; font-size: 11px; margin-right: 6px; }
  .class-name { width: 256px; }
  .class-sep { width: 26px; }
  .lesson-notes {
    position: absolute; left: 65px; top: 284px;
    font-size: 12.5px; letter-spacing: 0.2px; white-space: nowrap;
  }
</style>
</head>
<body>

<section class="card card-front" aria-label="Business card front">
  <div class="brand"><span class="brand-dot"></span><span class="brand-name">Open Door English</span></div>

  <svg class="stairs" width="597" height="331" viewBox="0 0 597 331" aria-hidden="true">
    <polyline points="40,122 276,122 276,158 338,158 338,194 398,194 398,231 457,231 457,286 542,286"
      fill="none" stroke="var(--teal)" stroke-width="1.6"/>
  </svg>

  <h1 class="person-name">Haruna Aoki</h1>
  <p class="person-role">English Instructor</p>

  <ul class="contact-list contact-primary">
    <li>
      <svg class="contact-icon" viewBox="0 0 13 13" aria-label="Phone"><circle cx="6.5" cy="6.5" r="6.5" fill="var(--teal)"/><path d="M4 3.2l1.3 0 .6 1.6-.8.6c.4.9 1 1.5 1.9 1.9l.6-.8 1.6.6v1.3c-3 .3-5.5-2.2-5.2-5.2z" fill="#fff"/></svg>
      <span>090-0000-4821</span>
    </li>
    <li>
      <svg class="contact-icon" viewBox="0 0 13 13" aria-label="Email"><circle cx="6.5" cy="6.5" r="6.5" fill="var(--teal)"/><rect x="3.3" y="4.3" width="6.4" height="4.4" fill="none" stroke="#fff" stroke-width="0.9"/><path d="M3.3 4.3l3.2 2.4 3.2-2.4" fill="none" stroke="#fff" stroke-width="0.9"/></svg>
      <span>haruna@mail.example</span>
    </li>
  </ul>

  <ul class="contact-list contact-social">
    <li><span class="contact-icon"></span><span>harunaaoki@chirp.example</span></li>
    <li><span class="contact-icon"></span><span>harunaaoki@friends.example</span></li>
    <li><span class="contact-icon"></span><span>www.harunaaoki.example</span></li>
  </ul>

  <div class="front-band"></div>
</section>

<section class="card card-back" aria-label="Business card back">
  <div class="back-panel">
    <span class="quote-mark quote-open">&ldquo;</span>
    <p class="quote">Feel free at asking me anything<br>about my classes</p>
    <span class="quote-mark quote-close">&rdquo;</span>

    <div class="divider"></div>

    <h2 class="classes-title">Classes:</h2>
    <ul class="class-list">
      <li><span class="class-name">Kids Class (Mom &amp; Dad can join)</span><span class="class-sep">-</span><span class="class-time">30 minutes / 45 minutes</span></li>
      <li><span class="class-name">Students (over age 13)</span><span class="class-sep">-</span><span class="class-time">60minutes / 90 minutes</span></li>
      <li><span class="class-name">Adult (over age 19)</span><span class="class-sep">-</span><span class="class-time">60 minutes / 90 minutes</span></li>
    </ul>

    <p class="lesson-notes">Price: from 3150 yen &nbsp;·&nbsp; Web &amp; Face to Face Lessons &nbsp;·&nbsp; Free Trial Lesson</p>
  </div>
</section>

</body>
</html>
```